Telecommunications/Power civil contractor needs business card design

Were a new telecommunications/power underground civil contractor that is looking for a new business card design. Our company colours are silver or grey and orange. Feel free to use the white background logo or the black background logo.

Target Market(s)

Local contractors, utility companies, private sector mining/energy companies, developers.

Industry/Entity Type

Telecommunications

Contact Information for Business Card

Each card will need the following info:
Persons name:
Title:
E-mail:
Phone number:
Shop Address:
Mailing Address:

Requirements
Must have
• Each card will need the following info:
• Persons name:
• Title:
• E-mail:
• Phone number:
• Shop Address:
• Mailing Address:

```html
<!DOCTYPE html>
<html lang="en">
<head>
<meta charset="utf-8">
<title>Ridgeline Contracting Inc — Business Card</title>
<link rel="stylesheet" href="https://fonts.googleapis.com/css2?family=Source+Sans+3:wght@400;600;700;800&display=swap">
<style>
  :root {
    --backdrop-top: #262626;
    --backdrop-bottom: #050505;
    --card-front: #f3f3f3;
    --card-back-top: #9c9c9c;
    --card-back-bottom: #7b7b7b;
    --orange: #ee5a24;
    --grey: #6b6b6b;
    --ink: #1c1c1c;
    --white: #ffffff;
  }
  html, body {
    margin: 0;
    width: 1200px;
    height: 900px;
    overflow: hidden;
  }
  body {
    position: relative;
    background: linear-gradient(180deg, var(--backdrop-top) 0%, #161616 55%, var(--backdrop-bottom) 100%);
    font-family: "Source Sans 3", "Myriad Pro", sans-serif;
  }
  .card {
    position: absolute;
    top: 184px;
    width: 302px;
    height: 490px;
    border-radius: 14px;
    box-shadow: 0 4px 14px rgba(0, 0, 0, 0.45);
    text-align: center;
    box-sizing: border-box;
  }
  .card--front {
    left: 299px;
    background: var(--card-front);
    color: var(--ink);
  }
  .card--back {
    left: 646px;
    background: linear-gradient(180deg, var(--card-back-top) 0%, #8a8a8a 50%, var(--card-back-bottom) 100%);
    color: var(--white);
  }
  .brand-mark {
    position: absolute;
    left: 90px;
    top: 26px;
  }
  .brand-name {
    position: absolute;
    left: 0;
    right: 0;
    margin: 0;
    font-weight: 800;
    text-transform: uppercase;
    line-height: 1;
  }
  .card--front .brand-name { top: 176px; color: var(--grey); }
  .card--back .brand-name { top: 186px; color: var(--white); }
  .brand-name__main {
    display: block;
    font-size: 36px;
    letter-spacing: 1px;
  }
  .brand-name__sub {
    display: block;
    font-size: 17px;
    letter-spacing: 1.6px;
    margin-top: 4px;
  }
  .person {
    position: absolute;
    top: 316px;
    left: 0;
    right: 0;
  }
  .person__name {
    margin: 0;
    font-size: 23px;
    font-weight: 600;
    color: var(--grey);
    line-height: 1.1;
  }
  .person__first { color: var(--orange); }
  .person__title {
    margin: 2px 0 0;
    font-size: 16px;
  }
  .contact {
    position: absolute;
    top: 412px;
    left: 0;
    right: 0;
    font-size: 16px;
    line-height: 25px;
  }
  .contact p { margin: 0; }
  .address {
    position: absolute;
    left: 0;
    right: 0;
    font-size: 17px;
    line-height: 19px;
  }
  .address p { margin: 0; }
  .address__label {
    font-size: 20px;
    font-weight: 700;
    line-height: 22px;
  }
  .address--shop { top: 280px; }
  .address--mailing { top: 380px; }
</style>
</head>
<body>
  <article class="card card--front" aria-label="Business card front">
    <svg class="brand-mark" width="122" height="122" viewBox="0 0 122 122" aria-hidden="true">
      <circle cx="61" cy="61" r="55" fill="none" stroke="var(--orange)" stroke-width="8"/>
    </svg>
    <h1 class="brand-name">
      <span class="brand-name__main">Ridgeline</span>
      <span class="brand-name__sub">Contracting Inc</span>
    </h1>
    <div class="person">
      <p class="person__name"><span class="person__first">Daniel</span> Carter</p>
      <p class="person__title">Managing Director</p>
    </div>
    <div class="contact">
      <p class="contact__phone">(044)-456-7890</p>
      <p class="contact__email">info@youremail.com</p>
    </div>
  </article>

  <article class="card card--back" aria-label="Business card back">
    <h2 class="brand-name">
      <span class="brand-name__main">Ridgeline</span>
      <span class="brand-name__sub">Contracting Inc</span>
    </h2>
    <div class="address address--shop">
      <p class="address__label">Shop Address:</p>
      <p>12345, Address Goes Here</p>
      <p>Country Name, 123456</p>
    </div>
    <div class="address address--mailing">
      <p class="address__label">Mailing Address:</p>
      <p>12345, Address Goes Here</p>
      <p>Country Name, 123456</p>
    </div>
  </article>
</body>
</html>
```